IT Company that provides secure IT solutions and services to our customers

We need business cards and a logo for a new IT Solutions company just created based in Kuala Lumpur, Malaysia. But will also be serving other countries in the region. We provide secure data, voice solutions on mobile platforms. Our first offering is encrypted voice and data solutions for IOS, Android, Windows and BlackBerry devices.

Target Market(s)

large organizations Govt, Police, Defence, Anti-corruption, Legal, highly regulated industries such as Health-care, Financial, Banking, Insurance,

Industry/Entity Type

Information Technology

Contact Information for Business Card

VelmoraNet (Logo - colour is ORVEX blue)Roshan Adeel Managing Director Kryption IT Sdn. Bhd.5th Floor, Block D, Wisma PLB,No.14 Jalan Seri Melor,50470, Kuala LumpurMalaysia

Font styles to use
Sans Serif

Colors
3176b5
ec1f27
fbed22

Requirements
Must have
• VelmoraNet all in Blue like ORVEX blue. A logo design perhaps a play of VN, K with a dangling T (colour can be any)
Nice to have
• I want a clean crisp card, not too busy, easy to read.

```html
<!DOCTYPE html>
<html lang="en">
<head>
<meta charset="utf-8">
<title>VelmoraNet Business Card</title>
<link rel="stylesheet" href="https://fonts.googleapis.com/css2?family=Open+Sans:wght@400;600;700;800&display=swap">
<style>
  :root {
    --backdrop: #3a322d;
    --card: #141414;
    --card-sheen: #2a2a2a;
    --red: #d4262b;
    --white: #ffffff;
    --light: #e6e6e6;
  }
  * { margin: 0; padding: 0; box-sizing: border-box; }
  html, body { width: 1200px; height: 844px; overflow: hidden; }
  body {
    background: var(--backdrop);
    font-family: "Open Sans", Arial, sans-serif;
    position: relative;
  }
  .card {
    position: absolute;
    top: 272px;
    width: 520px;
    height: 300px;
    background: radial-gradient(ellipse at 65% 35%, var(--card-sheen), var(--card) 70%);
    overflow: hidden;
  }
  .card--contact { left: 46px; }
  .card--brand { left: 634px; }

  .edge-band {
    position: absolute;
    left: 0; right: 0;
    height: 12px;
    background: var(--red);
  }
  .edge-band--top { top: 16px; }
  .edge-band--bottom { bottom: 16px; }

  .contact {
    position: absolute;
    left: 0; right: 0;
    top: 84px;
    text-align: center;
    color: var(--white);
  }
  .contact__name {
    display: inline-block;
    color: var(--red);
    font-weight: 700;
    font-size: 17px;
    letter-spacing: 0.5px;
    padding: 0 10px 2px;
    border-bottom: 1px solid var(--red);
  }
  .contact__role { font-size: 12px; margin-top: 3px; }
  .contact__company {
    color: var(--red);
    font-weight: 700;
    font-size: 14px;
    margin-top: 46px;
  }
  .contact__address { font-size: 13px; line-height: 1.5; margin-top: 2px; }

  .tab {
    position: absolute;
    width: 24px;
    height: 46px;
    background: var(--red);
    border-right: 3px solid var(--white);
  }
  .tab--left { left: 0; top: 196px; }
  .tab--right { right: 0; top: 32px; border-right: none; border-left: 3px solid var(--white); }

  .brand {
    position: absolute;
    left: 0; right: 0;
    top: 128px;
    display: flex;
    align-items: center;
    justify-content: center;
    gap: 14px;
  }
  .brand__mark {
    width: 40px; height: 40px;
    border: 3px solid var(--red);
    border-radius: 50%;
  }
  .brand__name {
    color: var(--light);
    font-weight: 800;
    font-size: 34px;
    letter-spacing: 0.5px;
  }
</style>
</head>
<body>
  <section class="card card--contact">
    <div class="edge-band edge-band--top"></div>
    <div class="contact">
      <div class="contact__name">ROSHAN ADEEL</div>
      <div class="contact__role">Managing Director</div>
      <div class="contact__company">VELMORA NET</div>
      <div class="contact__address">
        Sdn. Bhd. 5th Floor, Block D, Wisma<br>
        PLB, No.14 Jalan Seri Melor, 50470, Kuala Lumpur Malaysia
      </div>
    </div>
    <div class="edge-band edge-band--bottom"></div>
  </section>

  <section class="card card--brand">
    <div class="tab tab--right"></div>
    <div class="brand">
      <div class="brand__mark"></div>
      <div class="brand__name">VELMORANET</div>
    </div>
    <div class="tab tab--left"></div>
  </section>
</body>
</html>
```